Copperleaf Venture Trust

Take current power point presentation and make it uniform in color and font, and create designs that pop throughout the presentation. Right now, it is dull and mundane.

```html
<!DOCTYPE html>
<html lang="en">
<head>
<meta charset="utf-8">
<title>Copperleaf Venture Trust – Presentation Slides</title>
<link href="https://fonts.googleapis.com/css2?family=Poppins:wght@500;600&family=Roboto:wght@400;500;700&display=swap" rel="stylesheet">
<style>
:root{
  --blue:#0f5cb4;
  --blue-light:#d7e6f5;
  --panel-a:#edf2f8;
  --panel-b:#e2edf7;
  --ink:#1c1c1e;
  --text:#333;
  --muted:#666;
  --page:#d8d9dc;
  --white:#fff;
  --mark:#f1f1f2;
  --gray-icon:#8a8a8a;
}
*{box-sizing:border-box;margin:0;padding:0}
html,body{width:1026px;height:1200px;overflow:hidden;background:var(--page)}
body{position:relative;font-family:"Roboto",Arial,sans-serif;color:var(--text)}
.slide{position:absolute;width:443px;height:249px;background:var(--white);overflow:hidden;box-shadow:0 6px 14px rgba(0,0,0,.12)}
.col-l{left:51px}.col-r{left:531px}
.row-1{top:54px}.row-2{top:335px}.row-3{top:616px}.row-4{top:897px}
.abs{position:absolute}

.brand{position:absolute;display:flex;align-items:center;gap:4px;font-family:"Poppins",sans-serif;font-weight:600;color:var(--blue);font-size:19px;line-height:1;letter-spacing:.5px}
.brand .dot{width:7px;height:7px;background:var(--blue)}
.brand-head{right:26px;top:8px}

.bg-mark{position:absolute;left:-4px;bottom:4px;font-family:"Poppins",sans-serif;font-weight:600;font-size:74px;color:var(--mark);line-height:1;letter-spacing:2px}

.band{position:absolute;left:0;top:0;width:443px;height:37px}
.band-title{position:absolute;left:25px;top:9px;font-family:"Poppins",sans-serif;font-weight:500;font-size:12.5px;color:var(--white);letter-spacing:.3px}

.foot-line{position:absolute;left:0;top:236px;width:116px;height:1px;background:var(--blue)}
.foot-note{position:absolute;left:117px;top:232px;font-size:4.8px;color:var(--ink);white-space:nowrap}
.foot-note b{color:var(--blue);font-size:6px;margin-right:3px}
.page-no{position:absolute;left:403px;top:228px;width:17px;height:17px}
.page-no span{position:absolute;inset:0;display:flex;align-items:center;justify-content:center;font-size:4.8px;font-weight:700;color:var(--white)}

.sub-head{position:absolute;left:0;width:100%;text-align:center;font-weight:700;font-size:7px;color:var(--ink);text-decoration:underline;text-underline-offset:1.5px}
.lead{position:absolute;text-align:center;font-size:5.2px;line-height:8.5px;color:var(--ink)}

/* cover */
.cover-title{position:absolute;left:25px;top:72px;font-family:"Poppins",sans-serif;font-weight:500;font-size:16.5px;line-height:20px;color:var(--ink)}
.cover-title .blue{color:var(--blue)}
.cover-tag{position:absolute;left:25px;top:158px;width:125px;font-size:7px;line-height:10.5px;color:var(--ink)}

.divider-title{position:absolute;left:0;top:108px;width:100%;text-align:center;font-family:"Poppins",sans-serif;font-weight:600;font-size:26px;color:var(--ink);letter-spacing:.5px}
.divider-title span{color:var(--blue)}

/* disclosure */
.disc-col{position:absolute;top:56px;width:193px;font-size:5.05px;line-height:8.5px;text-align:justify;color:var(--ink)}
.disc-col p{margin-bottom:5px}

/* approach */
.orbit{position:absolute;left:43px;top:96px;width:122px;height:122px;border:0.8px dashed #9aa4b0;border-radius:50%}
.hub{position:absolute;left:55px;top:108px;width:98px;height:98px;border-radius:50%;background:var(--white);box-shadow:0 3px 10px rgba(0,0,0,.16);display:flex;align-items:center;justify-content:center}
.hub .brand{position:static;font-size:24px}
.node{position:absolute;width:3.5px;height:3.5px;border:0.8px solid var(--blue);border-radius:50%;background:var(--white)}
.feat-icon{position:absolute;width:26px;height:26px;border-radius:50%;background:var(--blue);border:2px solid #e6eef8;display:flex;align-items:center;justify-content:center}
.feat{position:absolute;width:210px}
.feat h4{font-size:5.2px;font-weight:700;color:var(--ink);margin-bottom:2px;position:relative}
.feat h4::before{content:"";position:absolute;left:-9px;top:0.5px;width:4px;height:4px;background:#8fb6e3;transform:rotate(45deg)}
.feat p{font-size:4.5px;line-height:6.8px;color:var(--ink)}

/* strategy cards */
.card{position:absolute;width:124px;height:78px;background:var(--white);border:1px solid var(--blue);border-radius:5px;box-shadow:0 3px 8px rgba(0,0,0,.12);padding:30px 11px 0}
.card.gray{border-color:#c9c9c9}
.card h4{font-size:6.6px;font-weight:500;color:var(--ink);margin-bottom:4px;letter-spacing:.2px}
.card p{font-size:5.2px;line-height:8.3px;color:var(--muted)}
.card-icon{position:absolute;width:34px;height:34px;border-radius:50%;background:var(--blue);display:flex;align-items:center;justify-content:center;border:2px solid var(--white)}
.card-icon.gray{background:var(--gray-icon)}

/* advantages */
.photo{position:absolute;border-radius:16px}
.adv-head{position:absolute;left:245px;top:84px;font-weight:700;font-size:8.5px;color:var(--ink);text-decoration:underline;text-underline-offset:2px}
.adv-list{position:absolute;left:245px;top:105px;width:180px;list-style:none}
.adv-list li{position:relative;padding-left:13px;font-size:5.6px;line-height:9px;color:var(--ink);margin-bottom:4.8px}
.adv-list li::before{content:"";position:absolute;left:0;top:2.2px;width:5px;height:5px;border-radius:50%;background:var(--blue)}
.adv-list li::after{content:"";position:absolute;left:1.3px;top:3.8px;width:1.5px;height:1.5px;border-top:0.8px solid #fff;border-right:0.8px solid #fff;transform:rotate(45deg)}
.adv-list b{font-weight:700}

/* competitive */
.pillar{position:absolute;top:82px;width:104px;height:129px;padding:52px 6px 0 7px}
.pillar.a{background:var(--panel-a)}.pillar.b{background:var(--panel-b)}
.pillar-icon{position:absolute;left:7px;top:9px;width:26px;height:26px;border-radius:50%;display:flex;align-items:center;justify-content:center}
.pillar-icon.gray{background:var(--gray-icon)}.pillar-icon.blue{background:var(--blue)}
.pillar h4{font-size:6.5px;font-weight:500;color:var(--ink);margin-top:-8px;margin-bottom:3px}
.pillar ul{padding-left:7px;list-style:none}
.pillar li{position:relative;font-size:4.2px;line-height:6.8px;color:#4a5a6a;margin-bottom:3px;padding-left:2px}
.pillar li::before{content:"";position:absolute;left:-5px;top:2.6px;width:1.8px;height:1.8px;border-radius:50%;background:var(--blue)}

/* diligence */
.dd-head{position:absolute;left:25px;top:52px;font-weight:700;font-size:7px;color:var(--ink);text-decoration:underline;text-underline-offset:1.5px}
.dd-lead{position:absolute;left:25px;top:68px;width:183px;font-size:5.2px;line-height:8.5px;color:var(--ink)}
.dd-icon{position:absolute;left:25px;width:27px;height:27px;border-radius:50%;background:var(--white);box-shadow:0 2px 6px rgba(0,0,0,.2);display:flex;align-items:center;justify-content:center}
.dd-item{position:absolute;left:68px;width:135px}
.dd-item h4{font-size:5.2px;font-weight:500;color:var(--ink);margin-bottom:2px}
.dd-item p{font-size:4.4px;line-height:6.7px;color:var(--ink)}
</style>
</head>
<body>

<svg width="0" height="0" style="position:absolute">
  <defs>
    <symbol id="band-shape" viewBox="0 0 443 37">
      <polygon points="0,0 332,0 309,35 0,35" fill="#0f5cb4"/>
      <polygon points="332,0 443,0 443,1.5 331,1.5" fill="#d7e6f5"/>
      <polygon points="0,35 309,35 308,37 0,37" fill="#d7e6f5"/>
    </symbol>
    <symbol id="diamond" viewBox="0 0 17 17">
      <rect x="2.5" y="2.5" width="12" height="12" fill="#0f5cb4" transform="rotate(45 8.5 8.5)"/>
    </symbol>
  </defs>
</svg>

<!-- Cover -->
<section class="slide col-l row-1">
  <svg class="abs" style="left:0;top:0" width="443" height="249" viewBox="0 0 443 249">
    <defs>
      <linearGradient id="cover-photo" x1="0" y1="0" x2="1" y2="1">
        <stop offset="0" stop-color="#b7b9ad"/>
        <stop offset=".45" stop-color="#8f8e6e"/>
        <stop offset=".75" stop-color="#8d7550"/>
        <stop offset="1" stop-color="#5e4c36"/>
      </linearGradient>
    </defs>
    <polygon points="128,0 443,0 443,249 266,249" fill="#f3f3f3"/>
    <polygon points="138,0 443,0 443,249 271,249" fill="url(#cover-photo)" role="img" aria-label="Photo of hands sheltering stacked coins with seedlings and a small tree growing on top"/>
    <polygon points="111,249 192,120 265,249" fill="#0f5cb4"/>
  </svg>
  <div class="brand" style="left:25px;top:14px"><span class="dot"></span>CVT</div>
  <h1 class="cover-title"><span class="blue">COPPERLEAF<br>VENTURE</span><br>TRUST</h1>
  <p class="cover-tag">Superior risk-adjusted returns while preserving capital in all market environments.</p>
</section>

<!-- Section divider -->
<section class="slide col-r row-1">
  <div class="bg-mark">CVT</div>
  <div class="brand brand-head"><span class="dot"></span>CVT</div>
  <h2 class="divider-title">SECTION <span>DIVIDER</span></h2>
  <div class="foot-line"></div>
  <p class="foot-note"><b>»</b>Please refer to the page entitled “General Notes and Risk Factors” when reviewing the information presented herein.</p>
  <div class="page-no"><svg width="17" height="17"><use href="#diamond"/></svg><span>05</span></div>
</section>

<!-- Disclosure -->
<section class="slide col-l row-2">
  <div class="bg-mark">CVT</div>
  <svg class="band"><use href="#band-shape"/></svg>
  <h2 class="band-title">DISCLOSURE</h2>
  <div class="brand brand-head"><span class="dot"></span>CVT</div>
  <div class="disc-col" style="left:25px">
    <p>This Presentation is a summary and does not constitute an offer to sell, or a solicitation of any offer to buy or sell, any securities. Any such offer will be made solely to qualified investors by means of an offering memorandum and related subscription materials, which will contain material information not contained herein. This Presentation is not intended to replace any such offering memorandum.</p>
    <p><b>No assurance can be given that the objectives discussed herein will be achieved and results may vary substantially on a quarterly, annual or other periodic basis. Past performance is not necessarily indicative of future results.</b></p>
    <p>Prospective reviewers should not construe this Presentation, any offering memorandum or any other communication received from CVT or its affiliates as legal, accounting, tax, investment or other advice, and each reviewer should consult with its own counsel and advisors as to all legal, tax, regulatory, financial and related matters.</p>
    <p>In addition, certain information contained herein has been provided by third parties and has not been independently verified by CVT.</p>
  </div>
  <div class="disc-col" style="left:226px">
    <p>CVT makes no representation or warranty, express or implied, as to the accuracy or the completeness of such information, and accepts no liability for any direct or consequential losses arising from the use of such information.</p>
    <p><b>This Presentation is confidential and proprietary to CVT.</b> Accordingly, this Presentation is to be treated as strictly confidential and not disclosed, directly or indirectly, to any party other than the person to whom it has been delivered and such person’s professional advisors. Any distribution of this Presentation, in whole or in part, or the divulgence of any of its contents, is unauthorized. No person has been authorized to give any information or make any representations other than as set forth herein.</p>
  </div>
  <div class="foot-line"></div>
  <p class="foot-note"><b>»</b>Please refer to the page entitled “General Notes and Risk Factors” when reviewing the information presented herein.</p>
  <div class="page-no"><svg width="17" height="17"><use href="#diamond"/></svg><span>02</span></div>
</section>

<!-- How we are different -->
<section class="slide col-r row-2">
  <div class="bg-mark">CVT</div>
  <svg class="band"><use href="#band-shape"/></svg>
  <h2 class="band-title">HOW WE ARE DIFFERENT</h2>
  <div class="brand brand-head"><span class="dot"></span>CVT</div>
  <h3 class="sub-head" style="top:46px">OUR DISTINCTIVE APPROACH</h3>
  <p class="lead" style="left:60px;top:62px;width:323px">Unlike many funds that adhere to a rigid transaction structure, CVT collaborates directly with each company to customize investment structures and strategies that align with mutual objectives.</p>
  <div class="orbit"></div>
  <div class="hub"><div class="brand"><span class="dot"></span>CVT</div></div>
  <span class="node" style="left:148px;top:112px"></span>
  <span class="node" style="left:163px;top:135px"></span>
  <span class="node" style="left:165px;top:165px"></span>
  <span class="node" style="left:152px;top:194px"></span>
  <div class="feat-icon" style="left:153px;top:87px"><svg width="12" height="12" viewBox="0 0 12 12"><rect x="2" y="1" width="7" height="9" rx="1" fill="none" stroke="#fff" stroke-width="1.2"/><path d="M4 4h3M4 6h3" stroke="#fff"/><circle cx="9" cy="9" r="2.4" fill="#fff"/></svg></div>
  <div class="feat-icon" style="left:171px;top:122px"><svg width="12" height="12" viewBox="0 0 12 12"><circle cx="6" cy="6" r="3" fill="none" stroke="#fff" stroke-width="1.3"/><path d="M6 0.8v2M6 9.2v2M0.8 6h2M9.2 6h2" stroke="#fff" stroke-width="1.3"/></svg></div>
  <div class="feat-icon" style="left:171px;top:158px"><svg width="12" height="12" viewBox="0 0 12 12"><path d="M2 8l3-3 2 2 3-4" fill="none" stroke="#fff" stroke-width="1.3"/><path d="M8 3h2v2" fill="none" stroke="#fff" stroke-width="1.2"/></svg></div>
  <div class="feat-icon" style="left:157px;top:195px"><svg width="12" height="12" viewBox="0 0 12 12"><path d="M3 7a2 2 0 010-4 3 3 0 015.5 0.5A1.8 1.8 0 019 7z" fill="#fff"/><path d="M6 7v3M3 10h6" stroke="#fff"/></svg></div>
  <div class="feat" style="left:196px;top:93px"><h4>FOCUSED PORTFOLIO</h4><p>We prioritize a smaller portfolio to maximize returns for each Investment.</p></div>
  <div class="feat" style="left:212px;top:126px"><h4>PROBLEM-SOLVING STRATEGY</h4><p>Our approach is centered on addressing challenges and/or supporting milestones to unlock each company’s full potential</p></div>
  <div class="feat" style="left:212px;top:162px"><h4>EFFICIENT PROCESSES</h4><p>CVT employs internal due diligence and document review procedures to ensure cost-effective and timely execution of opportunities.</p></div>
  <div class="feat" style="left:196px;top:200px"><h4>ROBUST NETWORK</h4><p>We leverage our established network of professionals and investment partners to explore new opportunities.</p></div>
  <div class="foot-line"></div>
  <p class="foot-note"><b>»</b>Please refer to the page entitled “General Notes and Risk Factors” when reviewing the information presented herein.</p>
  <div class="page-no"><svg width="17" height="17"><use href="#diamond"/></svg><span>06</span></div>
</section>

<!-- Investment strategy -->
<section class="slide col-l row-3">
  <div class="bg-mark">CVT</div>
  <svg class="band"><use href="#band-shape"/></svg>
  <h2 class="band-title">INVESTMENT STRATEGY</h2>
  <div class="brand brand-head"><span class="dot"></span>CVT</div>
  <h3 class="sub-head" style="top:46px">CVT FUNDING SPECIALIZATION</h3>
  <p class="lead" style="left:45px;top:63px;width:353px">CVT focuses on financing Development Stage, Emerging Growth, and Distressed public companies. This is achieved through a structured approach, wherein investments are tranched over a one- to four-year timeframe.</p>
  <h3 class="sub-head" style="top:91px">OBJECTIVES</h3>
  <p class="lead" style="left:0;top:106px;width:443px">Our strategy serves three key purposes:</p>
  <div class="card" style="left:25px;top:126px"><h4>MINIMIZE DILUTION</h4><p>Limits the dilution of the issuer’s common stock.</p></div>
  <div class="card gray" style="left:160px;top:143px"><h4>MITIGATE RISK</h4><p>Reduces exposure by allowing cessation of further investment in the event of a material adverse change.</p></div>
  <div class="card" style="left:294px;top:126px"><h4>PROTECT CAPITAL</h4><p>Safeguards against losses stemming from fraud or corporate malfeasance.</p></div>
  <div class="card-icon" style="left:37px;top:109px"><svg width="16" height="16" viewBox="0 0 16 16"><rect x="2" y="9" width="2.5" height="5" fill="#fff"/><rect x="6.5" y="7" width="2.5" height="7" fill="#fff"/><rect x="11" y="5" width="2.5" height="9" fill="#fff"/><path d="M2 7l4-3 3 2 5-4" fill="none" stroke="#fff" stroke-width="1.2"/></svg></div>
  <div class="card-icon gray" style="left:171px;top:126px"><svg width="16" height="16" viewBox="0 0 16 16"><circle cx="8" cy="8" r="5" fill="none" stroke="#fff" stroke-width="2" stroke-dasharray="2.2 1.3"/><circle cx="8" cy="8" r="3" fill="#fff"/><path d="M8 6.2v2" stroke="#8a8a8a"/><circle cx="8" cy="9.5" r=".5" fill="#8a8a8a"/></svg></div>
  <div class="card-icon" style="left:304px;top:109px"><svg width="16" height="16" viewBox="0 0 16 16"><circle cx="8" cy="3.5" r="1.8" fill="#fff"/><rect x="6.5" y="6" width="3" height="4" fill="#fff"/><path d="M2 8l3 5h6l3-5" fill="none" stroke="#fff" stroke-width="1.4"/></svg></div>
  <div class="foot-line"></div>
  <p class="foot-note"><b>»</b>Please refer to the page entitled “General Notes and Risk Factors” when reviewing the information presented herein.</p>
  <div class="page-no"><svg width="17" height="17"><use href="#diamond"/></svg><span>03</span></div>
</section>

<!-- Why direct investment -->
<section class="slide col-r row-3">
  <div class="bg-mark">CVT</div>
  <svg class="band"><use href="#band-shape"/></svg>
  <h2 class="band-title">WHY CVT’S DIRECT INVESTMENT STRATEGY?</h2>
  <div class="brand brand-head"><span class="dot"></span>CVT</div>
  <div class="photo" style="left:25px;top:62px;width:197px;height:149px;background:linear-gradient(135deg,#cfd6da 0%,#a9b3b8 45%,#7f8a8f 75%,#5f666a 100%)" role="img" aria-label="Photo of three colleagues gathered around a laptop in a bright office"></div>
  <h3 class="adv-head">KEY ADVANTAGES</h3>
  <ul class="adv-list">
    <li><b>Upside Potential:</b> Through strategic investments.</li>
    <li><b>Risk Management:</b> Achieved through tranching strategies.</li>
    <li><b>Equity Kickers:</b> Warrants or stock provide additional upside potential.</li>
    <li><b>Market Arbitrage/ Appreciation:</b> Achieved through tranching strategies.</li>
    <li><b>Robust Deal Flow:</b> Access to a vast pipeline of deals within various sectors.</li>
  </ul>
  <div class="foot-line"></div>
  <p class="foot-note"><b>»</b>Please refer to the page entitled “General Notes and Risk Factors” when reviewing the information presented herein.</p>
  <div class="page-no"><svg width="17" height="17"><use href="#diamond"/></svg><span>07</span></div>
</section>

<!-- Competitive advantage -->
<section class="slide col-l row-4">
  <div class="bg-mark">CVT</div>
  <svg class="band"><use href="#band-shape"/></svg>
  <h2 class="band-title">CVT’S COMPETITIVE ADVANTAGE</h2>
  <div class="brand brand-head"><span class="dot"></span>CVT</div>
  <p class="lead" style="left:0;top:49px;width:443px;font-size:6px">A Leading direct investment fund in a growing sector with beneficial liquidity terms.</p>
  <div class="pillar a" style="left:5px">
    <div class="pillar-icon gray"><svg width="13" height="13" viewBox="0 0 13 13"><circle cx="6.5" cy="4" r="2" fill="#fff"/><circle cx="2.8" cy="5" r="1.4" fill="#fff"/><circle cx="10.2" cy="5" r="1.4" fill="#fff"/><path d="M3 11a3.5 3.5 0 017 0z" fill="#fff"/></svg></div>
    <h4>PEOPLE</h4>
    <ul><li>Tight and established team and infrastructure. Additional use of outside professionals for reduced overhead and access to top talent.</li><li>Specialized experience with collateralized investments.</li><li>The members have invested or been involved with over $100 million for over 11 years through various market cycles.</li></ul>
  </div>
  <div class="pillar b" style="left:115px">
    <div class="pillar-icon blue"><svg width="13" height="13" viewBox="0 0 13 13"><circle cx="5" cy="5" r="2.5" fill="none" stroke="#fff" stroke-width="1.6" stroke-dasharray="1.5 1"/><circle cx="9" cy="9" r="1.8" fill="none" stroke="#fff" stroke-width="1.3" stroke-dasharray="1.2 .8"/></svg></div>
    <h4>PROCESS</h4>
    <ul><li>Proven and rigorous due diligence, portfolio construction and risk management processes.</li></ul>
  </div>
  <div class="pillar a" style="left:225px">
    <div class="pillar-icon gray"><svg width="13" height="13" viewBox="0 0 13 13"><circle cx="6.5" cy="6.5" r="4.5" fill="none" stroke="#fff" stroke-width="1.2"/><path d="M6.5 2a2.25 2.25 0 010 4.5 2.25 2.25 0 000 4.5" fill="none" stroke="#fff" stroke-width="1.2"/></svg></div>
    <h4>PHILOSOPHY</h4>
    <ul><li>To pair our rigorous diligence processes, with a disciplined investment approach and strong management to facilitate consistent performance.</li></ul>
  </div>
  <div class="pillar b" style="left:335px">
    <div class="pillar-icon blue"><svg width="13" height="13" viewBox="0 0 13 13"><rect x="2" y="8" width="2" height="3" fill="#fff"/><rect x="5.5" y="6" width="2" height="5" fill="#fff"/><rect x="9" y="4.5" width="2" height="6.5" fill="#fff"/><path d="M2 6l3.5-2.5 2 1.5 3.5-3" fill="none" stroke="#fff"/></svg></div>
    <h4>PERFORMANCE</h4>
    <ul><li>Consistent annual returns since inception (2015).</li><li>Long-term track record of performance by the Members.</li></ul>
  </div>
  <div class="foot-line"></div>
  <p class="foot-note"><b>»</b>Please refer to the page entitled “General Notes and Risk Factors” when reviewing the information presented herein.</p>
  <div class="page-no"><svg width="17" height="17"><use href="#diamond"/></svg><span>04</span></div>
</section>

<!-- Ongoing due diligence -->
<section class="slide col-r row-4">
  <div class="bg-mark">CVT</div>
  <svg class="band"><use href="#band-shape"/></svg>
  <h2 class="band-title">PROCESS – ON GOING DUE DILIGENCE</h2>
  <div class="brand brand-head"><span class="dot"></span>CVT</div>
  <h3 class="dd-head">ONGOING DUE DILIGENCE AND MONITORING</h3>
  <p class="dd-lead">Once an investment is made, the due diligence is typically performed on an ongoing and regular basis. This ongoing process involves analysis and evaluation of all relevant financial, legal, and accounting information, both historical and current.</p>
  <div class="dd-icon" style="top:113px"><svg width="14" height="14" viewBox="0 0 14 14"><path d="M3 7h2v6H3zM6 7l2-5 1 1-1 4h4l-1 6H6z" fill="#0f5cb4"/></svg></div>
  <div class="dd-icon" style="top:152px"><svg width="14" height="14" viewBox="0 0 14 14"><circle cx="6" cy="7" r="3.5" fill="none" stroke="#0f5cb4" stroke-width="2" stroke-dasharray="2 1.2"/><path d="M10 4h3M10 7h3M10 10h3" stroke="#0f5cb4"/></svg></div>
  <div class="dd-icon" style="top:193px"><svg width="14" height="14" viewBox="0 0 14 14"><circle cx="7" cy="4" r="2" fill="#0f5cb4"/><circle cx="3.5" cy="8.5" r="1.5" fill="#0f5cb4"/><circle cx="10.5" cy="8.5" r="1.5" fill="#0f5cb4"/><path d="M1 13a2.5 2.5 0 015 0zM8 13a2.5 2.5 0 015 0z" fill="#0f5cb4"/></svg></div>
  <div class="dd-item" style="top:118px"><h4>MONTHLY REVIEWS</h4><p>The team conducts monthly due diligence on portfolio companies to ensure continued oversight.</p></div>
  <div class="dd-item" style="top:154px"><h4>TRANCHING INTEGRATION</h4><p>This ongoing due diligence is closely aligned with the tranching strategy, providing a continuous framework for monitoring portfolio companies.</p></div>
  <div class="dd-item" style="top:194px"><h4>PROBLEM RESOLUTION</h4><p>If issues arise, the team can become more involved to safeguard investors’ rights and protect capital investments.</p></div>
  <div class="photo" style="left:222px;top:62px;width:196px;height:149px;background:linear-gradient(160deg,#eef0f1 0%,#d7dadc 45%,#a99a86 75%,#7d6a55 100%)" role="img" aria-label="Photo of rising coin stacks with seedlings and upward arrows"></div>
  <div class="foot-line"></div>
  <p class="foot-note"><b>»</b>Please refer to the page entitled “General Notes and Risk Factors” when reviewing the information presented herein.</p>
  <div class="page-no"><svg width="17" height="17"><use href="#diamond"/></svg><span>08</span></div>
</section>

</body>
</html>
```